A design led business card for the construction industry

High-end business card to match logo. White logo on dark grey/off black to the front. Matching dark font on white to back, possibly with logo design again.

We offer construction and project management services to commercial and private clients in the UK. Projetcs range from newbuilds, conversion of listed buildings and refurbishments and extensions of existing homes. Our focus is on quality and attention to detail using the highest skills.

Contact Information for Business Card

Name; Dorian Keble BSc
Position; Project Manager
Mobile; 07962 408 175
Tel; 01632 960457
email; dorian@stonevale.co.uk
web; www.stonevale.co.uk
Address; Ashcombe on Wye, KX4 7PW

Colors

Designer to choose only greyscale colors for use in the design.

Requirements
Must have
• To include the below description of the business,

CONSTRUCTION - PROJECT MANAGEMENT
Nice to have
• The posibility of the top back of the card being used as a ruler. So will have a measurement to scale in mm or an architect scale of 1:50
Should not have
• Should not be portrait

```html
<!DOCTYPE html>
<html lang="en">
<head>
<meta charset="utf-8">
<title>Stone Vale business card</title>
<link rel="stylesheet" href="https://fonts.googleapis.com/css2?family=Arimo:wght@400;700&display=swap">
<style>
  :root {
    --backdrop: #2b2c2e;
    --card-dark: #1d1e20;
    --card-light: #ffffff;
    --ink-light: #ffffff;
    --ink-dark: #1d1e20;
    --rule-light: #8a8b8e;
    --rule-dark: #9a9b9e;
    --pattern-tint: #f1f1f2;
  }
  * { box-sizing: border-box; margin: 0; padding: 0; }
  html, body { width: 1200px; height: 1108px; overflow: hidden; }
  body {
    background: var(--backdrop);
    font-family: "Arimo", Arial, sans-serif;
    position: relative;
  }
  .card {
    position: absolute;
    left: 300px;
    width: 600px;
    height: 388px;
    border-radius: 16px;
    overflow: hidden;
  }
  .card--front { top: 150px; background: var(--card-dark); color: var(--ink-light); }
  .card--back { top: 578px; background: var(--card-light); color: var(--ink-dark); }

  /* Front */
  .brand {
    position: absolute;
    top: 0; bottom: 0; left: 0;
    width: 270px;
    display: flex;
    flex-direction: column;
    align-items: center;
    justify-content: center;
  }
  .brand__square {
    width: 110px;
    height: 110px;
    border: 4px solid var(--ink-light);
  }
  .brand__name {
    margin-top: 24px;
    font-size: 22px;
    letter-spacing: 0.38em;
    padding-left: 0.38em;
    white-space: nowrap;
  }
  .divider {
    position: absolute;
    left: 270px;
    top: 60px;
    bottom: 60px;
    border-left: 1px solid var(--rule-light);
  }
  .person {
    position: absolute;
    top: 0; bottom: 0; left: 271px; right: 0;
    display: flex;
    flex-direction: column;
    justify-content: center;
    align-items: center;
    text-align: center;
  }
  .person__name { font-size: 21px; font-weight: 700; white-space: nowrap; }
  .person__name small { font-size: 16px; font-weight: 400; }
  .person__role { font-size: 16px; margin-top: 2px; }
  .icons {
    position: relative;
    margin-top: 12px;
    width: 260px;
    display: flex;
    justify-content: center;
    gap: 6px;
  }
  .icons::before, .icons::after {
    content: "";
    position: absolute;
    top: 50%;
    width: 48px;
    border-top: 1px solid var(--rule-light);
  }
  .icons::before { left: 0; }
  .icons::after { right: 0; }
  .icon {
    width: 28px; height: 28px;
    background: var(--ink-light);
    border-radius: 6px;
    display: flex; align-items: center; justify-content: center;
  }
  .contacts {
    margin-top: 10px;
    font-size: 17px;
    line-height: 1.25;
    white-space: nowrap;
  }
  .address {
    margin-top: 10px;
    width: 250px;
    padding-top: 8px;
    border-top: 1px solid var(--rule-light);
    font-size: 17px;
    white-space: nowrap;
  }

  /* Back */
  .ruler {
    position: absolute;
    top: 0; left: 0; right: 0;
    height: 46px;
    border-bottom: 1px solid var(--rule-dark);
  }
  .ruler__ticks {
    position: absolute;
    top: 0; left: 16px; right: 16px;
    height: 100%;
    background:
      repeating-linear-gradient(90deg, var(--ink-dark) 0 1px, transparent 1px 70.6px) top left / 100% 18px no-repeat,
      repeating-linear-gradient(90deg, var(--ink-dark) 0 1px, transparent 1px 35.3px) top left / 100% 12px no-repeat,
      repeating-linear-gradient(90deg, var(--ink-dark) 0 1px, transparent 1px 7.06px) top left / 100% 7px no-repeat;
  }
  .ruler__labels {
    position: absolute;
    top: 22px; left: 16px;
    font-size: 10px;
  }
  .ruler__labels span { position: absolute; transform: translateX(-50%); }
  .ruler__unit { position: absolute; top: 22px; right: 16px; font-size: 10px; letter-spacing: 0.1em; }
  .back-pattern {
    position: absolute;
    top: 47px; left: 0; right: 0; bottom: 0;
    background: linear-gradient(180deg, var(--pattern-tint), var(--card-light));
  }
  .back-content {
    position: absolute;
    top: 47px; left: 0; right: 0; bottom: 0;
    display: flex;
    flex-direction: column;
    align-items: center;
    justify-content: center;
    gap: 22px;
  }
  .back-mark {
    display: flex;
    align-items: center;
    gap: 10px;
    font-size: 18px;
    letter-spacing: 0.3em;
    white-space: nowrap;
  }
  .back-mark__square { width: 20px; height: 20px; border: 2px solid var(--ink-dark); }
  .tagline {
    font-size: 17px;
    letter-spacing: 0.04em;
    white-space: nowrap;
  }
</style>
</head>
<body>
  <section class="card card--front">
    <div class="brand">
      <div class="brand__square"></div>
      <div class="brand__name">STONE VALE</div>
    </div>
    <div class="divider"></div>
    <div class="person">
      <div class="person__name">DORIAN KEBLE <small>BSc</small></div>
      <div class="person__role">Project Manager</div>
      <div class="icons">
        <span class="icon" aria-label="mobile"><svg width="14" height="20" viewBox="0 0 14 20"><rect x="1.5" y="1" width="11" height="18" rx="2" fill="none" stroke="var(--ink-dark)" stroke-width="2"/><circle cx="7" cy="15.5" r="1.3" fill="var(--ink-dark)"/></svg></span>
        <span class="icon" aria-label="telephone"><svg width="20" height="18" viewBox="0 0 20 18"><path d="M2 6c0-3 16-3 16 0v2h-4V6H6v2H2z" fill="var(--ink-dark)"/><rect x="4" y="9" width="12" height="8" rx="1.5" fill="var(--ink-dark)"/></svg></span>
        <span class="icon" aria-label="email"><svg width="20" height="14" viewBox="0 0 20 14"><rect x="1" y="1" width="18" height="12" fill="none" stroke="var(--ink-dark)" stroke-width="2"/><path d="M1 1l9 7 9-7" fill="none" stroke="var(--ink-dark)" stroke-width="2"/></svg></span>
        <span class="icon" aria-label="website"><svg width="20" height="20" viewBox="0 0 20 20"><circle cx="10" cy="10" r="8" fill="none" stroke="var(--ink-dark)" stroke-width="2"/><path d="M2 10h16M10 2c-4 4-4 12 0 16M10 2c4 4 4 12 0 16" fill="none" stroke="var(--ink-dark)" stroke-width="1.5"/></svg></span>
      </div>
      <div class="contacts">
        <div>07962 408 175</div>
        <div>01632 960457</div>
        <div>dorian@stonevale.co.uk</div>
        <div>www.stonevale.co.uk</div>
      </div>
      <div class="address">Ashcombe on Wye, KX4 7PW</div>
    </div>
  </section>

  <section class="card card--back">
    <div class="ruler">
      <div class="ruler__ticks"></div>
      <div class="ruler__labels">
        <span style="left:0">0</span><span style="left:70.6px">1</span><span style="left:141.2px">2</span><span style="left:211.8px">3</span><span style="left:282.4px">4</span><span style="left:353px">5</span><span style="left:423.6px">6</span><span style="left:494.2px">7</span>
      </div>
      <div class="ruler__unit">CM</div>
    </div>
    <div class="back-pattern" role="img" aria-label="Faint repeating brand mark pattern across the card"></div>
    <div class="back-content">
      <div class="back-mark"><span class="back-mark__square"></span><span>STONE VALE</span></div>
      <div class="tagline">CONSTRUCTION - PROJECT MANAGEMENT</div>
    </div>
  </section>
</body>
</html>
```